We need a design for a Tequila line that will be infused with cannabis oil.
The design should have at least the following items.

The name Morello Tequila
Marijuana leaf
200 ml fluid
500 mg THC

The lable to be printed will be clear "see through"
The liquid inside the clear bottle will be light gold in color.

Target Market(s)

Marijuana users

Requirements
Must have
• Marijuana leaf
• must say 200 ml
• must say 500 mg thc
Nice to have
• bottle lable will be clear on clear bottle.

```html
<!DOCTYPE html>
<html lang="en">
<head>
<meta charset="utf-8">
<title>Morello Tequila – Clear Label</title>
<link rel="stylesheet" href="https://fonts.googleapis.com/css2?family=IM+Fell+English+SC&family=Arimo:wght@700&display=swap">
<style>
  :root {
    --liquid-gold: #c9c97a;
    --liquid-light: #dcdc97;
    --ink-slate: #2c3636;
    --leaf-teal: #2fa886;
    --leaf-deep: #1f8a72;
  }
  html, body {
    margin: 0;
    padding: 0;
    overflow: hidden;
  }
  .canvas {
    width: 785px;
    height: 1200px;
    background: radial-gradient(ellipse at 50% 45%, var(--liquid-light), var(--liquid-gold));
    position: relative;
    overflow: hidden;
  }
  .label-art {
    position: absolute;
    inset: 0;
    width: 785px;
    height: 1200px;
  }
  .brand-arc {
    font-family: "IM Fell English SC", serif;
    font-size: 78px;
    letter-spacing: 18px;
    fill: var(--ink-slate);
  }
  .spec-text {
    font-family: "Arimo", sans-serif;
    font-weight: 700;
    font-size: 17px;
    fill: var(--ink-slate);
  }
  .spec-rule {
    stroke: var(--ink-slate);
    stroke-width: 2;
  }
</style>
</head>
<body>
<div class="canvas">
  <svg class="label-art" viewBox="0 0 785 1200" xmlns="http://www.w3.org/2000/svg">
    <defs>
      <path id="arc-top" d="M 150 640 A 242 242 0 0 1 634 640"/>
      <path id="arc-bottom" d="M 122 600 A 270 270 0 0 0 662 600"/>
      <radialGradient id="leaf-tone" cx="50%" cy="50%" r="50%">
        <stop offset="0%" stop-color="var(--leaf-teal)"/>
        <stop offset="100%" stop-color="var(--leaf-deep)" stop-opacity="0.85"/>
      </radialGradient>
    </defs>

    <text class="brand-arc">
      <textPath href="#arc-top" startOffset="50%" text-anchor="middle">MORELLO</textPath>
    </text>

    <ellipse class="leaf-emblem" role="img" aria-label="Cannabis leaf illustration"
             cx="392" cy="630" rx="165" ry="130" fill="url(#leaf-tone)"/>

    <text class="brand-arc">
      <textPath href="#arc-bottom" startOffset="50%" text-anchor="middle">TEQUILA</textPath>
    </text>

    <text class="spec-text" x="182" y="935">200 ml</text>
    <text class="spec-text" x="608" y="935" text-anchor="end">500 mg THC</text>
    <line class="spec-rule" x1="180" y1="944" x2="608" y2="944"/>
  </svg>
</div>
</body>
</html>
```